Webdesign für Projektmanagement
Zielgruppe
Projektmanagement und Projektsteuerung von Bauvorhaben für Projektentwickler und Bauträger.
Wesentliche Bereiche sind Wirtschaftliche Steuerung, Steuerung der Baustelle und Bauabläufe sowie Steuerung der Marketing und Vertriebsaktivitäten.
Aufgabenstellung
Orientierung am Logo. Logo und Visitenkarte liegen bei. Schriftart Prelo und Prelo Slab.

```html
<!DOCTYPE html>
<html lang="de">
<head>
<meta charset="utf-8">
<title>Hallberg Real Estate – Projektmanagement</title>
<link rel="stylesheet" href="https://fonts.googleapis.com/css2?family=Raleway:ital,wght@0,200;0,300;0,400;0,500;0,700;1,300;1,400&family=Roboto+Slab:wght@700&display=swap">
<style>
  :root{
    --stage:#03233f;
    --navy:#0c2643;
    --gold:#a38c3e;
    --olive-light:#c8b983;
    --olive:#b3a265;
    --olive-dark:#9c8b52;
    --bar:rgba(120,104,52,.35);
    --card:rgba(240,239,236,.93);
    --text:#3b3b3b;
    --muted:#6b6b6b;
    --line:#ececec;
    --white:#ffffff;
  }
  *{box-sizing:border-box;margin:0;padding:0}
  html,body{width:1036px;height:1200px;overflow:hidden}
  body{background:var(--stage);font-family:"Raleway",sans-serif;position:relative}
  .site{position:absolute;left:0;top:301px;width:1036px;height:597px;display:flex}
  .sidebar{width:158px;height:100%;background:var(--white);position:relative}
  .brand{position:absolute;left:24px;top:52px;display:flex;align-items:center;gap:6px}
  .brand-name{font-family:"Roboto Slab",serif;font-weight:700;font-size:23px;color:var(--navy);letter-spacing:-.3px}
  .brand-mark{width:7px;height:7px;background:var(--gold)}
  .nav{position:absolute;left:0;top:144px;width:158px;list-style:none;border-top:1px solid var(--line)}
  .nav li{height:32px;border-bottom:1px solid var(--line);display:flex;align-items:center;justify-content:space-between;padding:0 18px 0 24px;font-size:9px;font-weight:500;color:var(--navy);letter-spacing:.2px}
  .nav li.active{color:var(--gold);font-weight:700}
  .nav .chev{width:5px;height:8px}
  .nav li.search{justify-content:flex-start;gap:7px;color:#9a9a9a;font-style:italic;font-weight:400}
  .social{position:absolute;left:34px;top:566px;display:flex;gap:10px}
  .social span{width:10px;height:10px;border-radius:50%;background:var(--navy)}
  .main{flex:1;position:relative;overflow:hidden}
  .hero-photo{position:absolute;inset:0;background:
      radial-gradient(ellipse at 78% 45%, rgba(150,125,70,.55), transparent 45%),
      radial-gradient(ellipse at 30% 90%, rgba(140,118,66,.45), transparent 50%),
      linear-gradient(160deg,var(--olive-light) 0%,var(--olive) 55%,var(--olive-dark) 100%)}
  .topbar{position:absolute;left:0;top:0;right:0;height:30px;background:var(--bar);display:flex;align-items:center;gap:16px;padding-left:55px;font-size:8.6px;color:var(--white)}
  .topbar span{display:flex;align-items:center;gap:5px}
  .topbar svg{width:9px;height:9px}
  .kicker{position:absolute;left:55px;top:138px;font-size:15.5px;font-weight:700;color:var(--navy);letter-spacing:.3px}
  .headline{position:absolute;left:54px;top:166px;font-size:49px;line-height:58px;font-weight:200;color:var(--white);letter-spacing:1.5px}
  .cards{position:absolute;left:55px;top:312px;display:flex;gap:9px}
  .card{width:244px;height:146px;background:var(--card);position:relative;padding:12px 12px 0 12px}
  .card-label{font-size:8.5px;font-style:italic;color:var(--muted)}
  .card-title{margin-top:8px;font-size:10px;line-height:13px;color:var(--gold);font-weight:400}
  .card-text{margin-top:7px;font-size:8.2px;line-height:13.5px;color:var(--text);font-weight:400}
  .card-more{position:absolute;right:0;bottom:0;width:79px;height:21px;background:var(--navy);color:var(--white);font-size:7.6px;font-weight:700;display:flex;align-items:center;justify-content:center;letter-spacing:.2px}
  .footer{position:absolute;left:0;right:0;bottom:0;height:36px;background:rgba(110,96,52,.18);font-size:8.6px;color:#5b5239;display:flex;align-items:center;padding-left:55px}
</style>
</head>
<body>
<div class="site">
  <aside class="sidebar">
    <div class="brand"><span class="brand-name">Hallberg</span><span class="brand-mark"></span></div>
    <ul class="nav">
      <li class="active">HOME</li>
      <li>LEISTUNGEN</li>
      <li>ÜBER UNS<svg class="chev" viewBox="0 0 5 8"><path d="M1 1l3 3-3 3" fill="none" stroke="#a38c3e" stroke-width="1"/></svg></li>
      <li>PROJEKTE<svg class="chev" viewBox="0 0 5 8"><path d="M1 1l3 3-3 3" fill="none" stroke="#a38c3e" stroke-width="1"/></svg></li>
      <li>PARTNER</li>
      <li>KONTAKT</li>
      <li class="search"><svg width="7" height="7" viewBox="0 0 8 8"><circle cx="3.2" cy="3.2" r="2.3" fill="none" stroke="#a38c3e" stroke-width="1.2"/><path d="M5 5l2.4 2.4" stroke="#a38c3e" stroke-width="1.3"/></svg>Suchen</li>
    </ul>
    <div class="social"><span></span><span></span><span></span><span></span></div>
  </aside>
  <main class="main">
    <div class="hero-photo" role="img" aria-label="Foto eines Turms aus Holzklötzen auf einem Tisch, warm gelb getönt"></div>
    <div class="topbar">
      <span><svg viewBox="0 0 10 10"><path d="M2 .8l1.6 2-1 1.1a6 6 0 0 0 3.5 3.5l1.1-1 2 1.6-1 1.6C4.5 9.5.5 5.5.4 1.8z" fill="#0c2643"/></svg>+49 (0)211 - 555 123 40</span>
      <span><svg viewBox="0 0 10 10"><circle cx="5" cy="5" r="4.2" fill="none" stroke="#0c2643" stroke-width="1"/><path d="M5 2.6V5h2" fill="none" stroke="#0c2643" stroke-width="1"/></svg>Mo - Fr 9:00 - 18:00</span>
      <span><svg viewBox="0 0 10 10"><rect x=".5" y="2" width="9" height="6" fill="none" stroke="#0c2643" stroke-width="1"/><path d="M.5 2l4.5 3.5L9.5 2" fill="none" stroke="#0c2643" stroke-width="1"/></svg>info@hallberg-re.de</span>
      <span><svg viewBox="0 0 10 10"><path d="M5 .5a3.3 3.3 0 0 1 3.3 3.3C8.3 6.3 5 9.6 5 9.6S1.7 6.3 1.7 3.8A3.3 3.3 0 0 1 5 .5z" fill="#0c2643"/><circle cx="5" cy="3.8" r="1.2" fill="#b3a265"/></svg>Lindenallee 12, 40210 Düsseldorf</span>
    </div>
    <h2 class="kicker">PROJEKTMANAGEMENT &amp; PROJEKTSTEUERUNG</h2>
    <h1 class="headline">WIR REALISIEREN<br>BAUVORHABEN</h1>
    <div class="cards">
      <article class="card">
        <p class="card-label">Betriebswirtschaftliche Planung</p>
        <h3 class="card-title">STET CLITA KASD GUBERGREN NO SEA<br>TAKIMATA SANCTUS EST LOREM IPSUM</h3>
        <p class="card-text">Lorem ipsum dolor sit amet, consetetur sadipscing elitr, sed diam nonumy eirmod tempor invidunt ut labore et dolore magna aliquyam erat, sed diam voluptua.</p>
        <span class="card-more">WEITERLESEN</span>
      </article>
      <article class="card">
        <p class="card-label">Steuerung der baulichen Umsetzung</p>
        <h3 class="card-title">STET CLITA KASD GUBERGREN NO SEA<br>TAKIMATA SANCTUS EST LOREM IPSUM</h3>
        <p class="card-text">Lorem ipsum dolor sit amet, consetetur sadipscing elitr, sed diam nonumy eirmod tempor invidunt ut labore et dolore magna aliquyam erat, sed diam voluptua.</p>
        <span class="card-more">WEITERLESEN</span>
      </article>
      <article class="card">
        <p class="card-label">Marketing und Vertrieb</p>
        <h3 class="card-title">STET CLITA KASD GUBERGREN NO SEA<br>TAKIMATA SANCTUS EST LOREM IPSUM</h3>
        <p class="card-text">Lorem ipsum dolor sit amet, consetetur sadipscing elitr, sed diam nonumy eirmod tempor invidunt ut labore et dolore magna aliquyam erat, sed diam voluptua.</p>
        <span class="card-more">WEITERLESEN</span>
      </article>
    </div>
    <footer class="footer">© 2017 Hallberg Real Estate GmbH - Impressum</footer>
  </main>
</div>
</body>
</html>
```